Wordpress Website design partner needed for an Arabic Language Institute for English Speakers

We are an online Arabic Language institute, targeting English Speakers around the world and we provide online courses and private group and one on one classes
We are looking for a total of 5 pages designed.
The Design should be mobile-first, and then provide PC for any differences.
I am looking for a consistent design with a lot of white space and in line with our Logo colours.
Images used should be around the theme of Arabic Language/Islamic in Nature, so please do not use any illustrations or images of animals or human beings except for silhouettes or images without faces visible, such as someone facing other way or below torso or hands etc.
The website will eventually be prepared for Wordpress using Divi.
I will provide a very structured outline of what elements and modules each page should have. Therefore I am looking for someone that has an eye for detail and is precise in executing requirements.
I decided to post on this site because I am looking for a long-term partner that can take care of any of our design needs as they come up.
More details to follow
I will do abit more research tomorrow to suggest sample sites
Updates
Target Market(s)
English speakers that want to learn Arabic for Religous purposes such as understanding the Quran
Industry/Entity Type
Education
Colors
Designer to choose colors to be used in the design.
Requirements
Must have
- Mobile First, and design for PC for changes
- Consistency
- Plenty of White Space
- Colour Palette based on Logo
- Colour and Transparent/White Header for when scrolling
- Big Call to Action buttons with contrasting colors
- A consistent footer for all pages with
- -Social Media Icons
- -Contact us
- -Sitemap
- -Copyright
- -Logo
- Anything with a hashtag (#) beforehand in the Doc file means it should be a module like the modules used in Divi Theme, Please check the following website for an explanation of what each module consists of and some examples of it in use. https://www.pelmorashowcase.net/pelmora-blocks-guide/
Nice to have
- Parallax Effect
Should not have
- illustrations or images of animals or human beings except for silhouettes or images without faces visible, such as someone facing other way or below torso or hands etc.

```html
<!DOCTYPE html>
<html lang="en">
<head>
<meta charset="utf-8">
<title>Al-Noor Arabic Academy</title>
<link rel="stylesheet" href="https://fonts.googleapis.com/css2?family=Montserrat:wght@500;600;700&family=Roboto:wght@400;500;700&display=swap">
<style>
:root{
  --blue-deep:#1b5c9e;
  --blue-mid:#1e74b0;
  --teal:#2a93aa;
  --accent:#1a8fb0;
  --ink:#222;
  --grey:#8a8a8a;
  --grey-light:#f4f4f4;
  --footer:#2b2b2b;
  --white:#fff;
}
*{box-sizing:border-box;margin:0;padding:0}
html,body{width:1200px;height:3912px;overflow:hidden}
body{position:relative;font-family:"Roboto",sans-serif;color:var(--ink);background:var(--white)}
.section{position:absolute;left:0;width:1200px;overflow:hidden}
.abs{position:absolute}
.center{text-align:center;left:0;width:1200px}
h2.section-title{position:absolute;left:0;width:1200px;text-align:center;font-family:"Roboto",sans-serif;font-weight:700;font-size:36px;color:var(--blue-deep)}
.btn-outline{position:absolute;border:2px solid var(--white);color:var(--white);font-weight:700;font-size:15px;display:flex;align-items:center;justify-content:center;gap:12px;border-radius:3px}

/* header */
.site-header{top:0;height:106px;background:var(--white);z-index:3;overflow:visible}
.logo-badge{position:absolute;left:137px;top:-40px;width:144px;height:184px;border-radius:0 0 72px 72px;background:var(--white);display:flex;flex-direction:column;align-items:center;justify-content:flex-end;padding-bottom:34px}
.logo-badge .mark{width:34px;height:34px;background:var(--blue-mid);margin-bottom:8px}
.logo-badge .name{font-family:"Roboto",sans-serif;font-weight:700;font-size:13px;color:var(--blue-deep);letter-spacing:1px;text-align:center;line-height:1.3}
.main-nav{position:absolute;top:43px;left:0;width:1200px;height:20px}
.main-nav a{position:absolute;font-size:15px;font-weight:700;color:#333;text-decoration:none}
.main-nav a.active{color:var(--accent)}
.main-nav a.active::after{content:"";position:absolute;left:0;right:0;top:26px;height:2px;background:var(--accent)}

/* intro bar */
.intro-bar{top:106px;height:149px;background:linear-gradient(90deg,var(--blue-mid),var(--teal))}
.intro-bar p{position:absolute;left:144px;top:52px;width:560px;color:var(--white);font-weight:700;font-size:14.5px;line-height:24px}
.play-icon{width:22px;height:22px;border-radius:50%;background:var(--white);display:flex;align-items:center;justify-content:center}

/* hero */
.hero{top:255px;height:631px}
.hero-photo{position:absolute;inset:0;background:radial-gradient(circle at 18% 55%,#f5b13a 0,#c45a12 22%,transparent 45%),linear-gradient(180deg,#e9c569 0%,#d98c35 35%,#8a3a12 75%,#3a1608 100%)}
.hero-brand{position:absolute;top:236px;font-family:"Montserrat",sans-serif;font-weight:700;font-size:55px;letter-spacing:14px;color:var(--white)}
.hero-sub{position:absolute;top:305px;font-family:"Montserrat",sans-serif;font-weight:500;font-size:26px;letter-spacing:9px;color:var(--white)}
.hero-text{position:absolute;top:368px;font-weight:700;font-size:15.5px;line-height:24px;color:var(--white)}
.slider-arrow{position:absolute;top:295px}
.dots{position:absolute;top:568px;left:578px;display:flex;gap:8px}
.dots span{width:8px;height:8px;border-radius:50%;background:var(--white)}
.dots span.on{background:var(--accent)}

/* benefits */
.benefits{top:886px;height:471px;background:linear-gradient(180deg,#fafafa,#eeeeee)}
.skyline{position:absolute;left:0;bottom:0;width:1200px;height:300px;background:linear-gradient(180deg,rgba(220,220,220,0),rgba(205,205,205,.55))}
.benefit{position:absolute;top:177px;width:240px;text-align:center}
.benefit .icon{width:76px;height:76px;margin:0 auto 38px;border-radius:8px;background:linear-gradient(180deg,#f0cf3a,#333)}
.benefit h3{font-size:15px;font-weight:700;color:#333;margin-bottom:14px}
.benefit p{font-size:12px;line-height:20px;color:var(--grey)}

/* testimonial */
.testimonial{top:1357px;height:387px;background:var(--grey-light)}
.quote{position:absolute;width:300px}
.quote .badge{position:absolute;left:-113px;top:-13px;width:94px;height:94px;border-radius:50%;background:linear-gradient(135deg,var(--blue-mid),var(--blue-deep));color:var(--white);font-family:Georgia,serif;font-size:70px;font-weight:700;display:flex;align-items:center;justify-content:center;padding-top:22px}
.quote p{font-size:12px;line-height:19px;color:var(--grey)}
.quote .who{font-size:12px;font-weight:700;color:#222;margin-top:10px}
.quote .role{font-size:11.5px;color:var(--accent);margin-left:6px;margin-top:4px}

/* launch */
.launch{top:1744px;height:762px}
.night-photo{position:absolute;inset:0;background:linear-gradient(180deg,#0c1a40 0%,#1d3570 30%,#16264f 55%,#5a2a2a 68%,#d4551c 72%,#7a2a16 80%,#150c10 100%)}
.launch h2{position:absolute;top:174px;font-family:"Roboto",sans-serif;font-size:36px;font-weight:700;color:var(--white);line-height:46px}
.launch .when{position:absolute;top:476px;font-size:30px;font-weight:500;color:var(--white)}
.count{position:absolute;top:540px;width:140px;text-align:center;color:var(--white)}
.count b{display:block;font-size:36px;font-weight:500}
.count span{font-size:15px}
.colon{position:absolute;top:552px;color:var(--white);font-size:30px;font-weight:700}

/* features */
.features{top:2506px;height:809px;background:linear-gradient(180deg,#f2fafd,#d9eef6)}
.skyline-blue{position:absolute;left:0;bottom:0;width:1200px;height:440px;background:linear-gradient(180deg,rgba(160,215,235,0),rgba(130,200,228,.55))}
.accordion{position:absolute;left:301px;width:598px}
.acc-item{position:absolute;left:0;width:598px;height:46px;background:#f4f4f4;border:1px solid #dcdcdc;font-size:14px;color:#333;padding:14px 24px}
.acc-item::after{content:"";position:absolute;right:24px;top:17px;width:12px;height:12px;border-radius:50%;background:#666}
.acc-item.open{background:var(--white);height:148px}
.acc-item.open p{font-size:12px;line-height:20px;color:var(--grey);margin-top:24px}
.partner{position:absolute;top:3228px;font-size:30px;font-weight:700;color:#1f4f8a;display:flex;align-items:center;gap:10px}
.partner i{display:block;width:34px;height:34px;border-radius:50%;background:#1f4f8a}

/* contact */
.touch{top:3315px;height:411px;background:linear-gradient(90deg,var(--blue-mid),var(--teal))}
.touch h2{position:absolute;left:143px;top:85px;font-size:36px;font-weight:700;color:var(--white)}
.touch p{position:absolute;left:145px;top:158px;width:440px;font-size:12px;line-height:21.5px;color:var(--white)}
.field{position:absolute;left:732px;width:324px;height:53px;background:var(--white);font-size:13px;color:#555;padding:18px 24px}
.join{left:732px;top:271px;width:324px;height:52px}

/* footer */
.site-footer{top:3726px;height:186px;background:var(--footer)}
.foot-logo{position:absolute;left:146px;top:28px;width:100px;text-align:center;color:var(--white);font-weight:700;font-size:13px;letter-spacing:1px;line-height:1.4}
.foot-logo .mark{width:50px;height:50px;background:var(--white);margin:0 auto 14px}
.ring{position:absolute;width:42px;height:42px;border:2px solid var(--white);border-radius:50%;display:flex;align-items:center;justify-content:center;color:var(--white);font-size:10px;font-weight:700}
.foot-text{position:absolute;color:var(--white);font-size:12.5px}
.copy{position:absolute;left:324px;top:122px;color:var(--white);font-size:11px}
</style>
</head>
<body>

<header class="section site-header">
  <div class="logo-badge">
    <div class="mark"></div>
    <div class="name">AL-NOOR<br>ARABIC ACADEMY</div>
  </div>
  <nav class="main-nav">
    <a class="active" href="#" style="left:471px">HOME</a>
    <a href="#" style="left:556px">ABOUT US</a>
    <a href="#" style="left:671px">CONTACT US</a>
    <a href="#" style="left:805px">COURSE PAGE</a>
    <a href="#" style="left:949px">OUR COURSES</a>
  </nav>
</header>

<section class="section intro-bar">
  <p>The Arabic Language Academy which helps understand Allah's words and the Noble Prophets teachings directly in the most Effective, Efficient and Effortless way. Never rely on translations again!</p>
  <a class="btn-outline" style="left:811px;top:63px;width:243px;height:51px">START LEARNING NOW <span class="play-icon"><svg width="10" height="10" viewBox="0 0 10 10"><path d="M2 1l7 4-7 4z" fill="#1e74b0"/></svg></span></a>
</section>

<section class="section hero">
  <div class="hero-photo" role="img" aria-label="Photograph of a glowing ornate Arabic lantern before warm desert dunes at sunset"></div>
  <div class="hero-brand center">AL-NOOR</div>
  <div class="hero-sub center">ARABIC ACADEMY</div>
  <p class="hero-text center">Lorem ipsum dolor sit amet, consectetur adipiscing elit, sed do eiusmod tempor<br>incididunt ut labore et dolore magnum suspendisse ultrices gravida.</p>
  <a class="btn-outline" style="left:518px;top:451px;width:164px;height:51px">GET STARTED</a>
  <svg class="slider-arrow" style="left:46px" width="30" height="52" viewBox="0 0 30 52"><path d="M26 4L6 26l20 22" fill="none" stroke="#fff" stroke-width="5" opacity=".8"/></svg>
  <svg class="slider-arrow" style="left:1122px" width="30" height="52" viewBox="0 0 30 52"><path d="M4 4l20 22L4 48" fill="none" stroke="#fff" stroke-width="5" opacity=".8"/></svg>
  <div class="dots"><span></span><span class="on"></span><span></span></div>
</section>

<section class="section benefits">
  <div class="skyline" role="img" aria-label="Faint grey mosque skyline with minarets and domes"></div>
  <h2 class="section-title" style="top:84px">Benefits</h2>
  <div class="benefit" style="left:138px"><div class="icon" role="img" aria-label="Dome with crescent icon"></div><h3>EFFICIENT</h3><p>Lorem ipsum dolor sit amet, consectetur adipiscing elit, sed do eiusmod tempor incididunt ut labore et gravida.</p></div>
  <div class="benefit" style="left:475px"><div class="icon" role="img" aria-label="Open book on a stand icon"></div><h3>EFFECTIVE</h3><p>Lorem ipsum dolor sit amet, consectetur adipiscing elit, sed do eiusmod tempor incididunt ut labore etgravida.</p></div>
  <div class="benefit" style="left:811px"><div class="icon" role="img" aria-label="Mosque building icon"></div><h3>EFFORTLESS</h3><p>Lorem ipsum dolor sit amet, consectetur adipiscing elit, sed do eiusmod tempor incididunt ut labore et gravida.</p></div>
</section>

<section class="section testimonial">
  <h2 class="section-title" style="top:88px">Testimonial</h2>
  <div class="quote" style="left:273px;top:192px"><div class="badge">&ldquo;</div><p>Lorem ipsum dolor sit amet, consectetur adipiscing elit, sed do eiusmod tempor incididunt ut labore et dolore magnempor iempora aliqua.</p><div class="who">- DANIEL REED</div><div class="role">Client</div></div>
  <div class="quote" style="left:753px;top:192px"><div class="badge">&ldquo;</div><p>Lorem ipsum dolor sit amet, consectetur adipiscing elit, sed do eiusmod tempor incididunt ut labore et dolore magnempor iempora aliqua.</p><div class="who">- DANIEL REED</div><div class="role">Client</div></div>
</section>

<section class="section launch">
  <div class="night-photo" role="img" aria-label="Night sky with crescent moon and clouds over a sunset city skyline"></div>
  <h2 class="center">7 Learning Strategies that will boost<br>your Arabic Learning Instantly</h2>
  <a class="btn-outline" style="left:494px;top:323px;width:212px;height:51px">BOOK YOUR SPOT</a>
  <div class="when center">Launching In</div>
  <div class="count" style="left:191px"><b>000</b><span>DAYS</span></div>
  <div class="colon" style="left:361px">:</div>
  <div class="count" style="left:410px"><b>00</b><span>HOURS</span></div>
  <div class="colon" style="left:586px">:</div>
  <div class="count" style="left:632px"><b>00</b><span>MINUTES</span></div>
  <div class="colon" style="left:820px">:</div>
  <div class="count" style="left:863px"><b>00</b><span>SECONDS</span></div>
</section>

<section class="section features">
  <div class="skyline-blue" role="img" aria-label="Soft watercolour mosque skyline in pale blue"></div>
  <h2 class="section-title" style="top:102px">Features</h2>
  <div class="accordion" style="top:170px">
    <div class="acc-item" style="top:0">24/7 Access</div>
    <div class="acc-item" style="top:58px">Learn at your own Pace</div>
    <div class="acc-item" style="top:117px">Certificate</div>
    <div class="acc-item" style="top:175px">Free Study Material</div>
    <div class="acc-item open" style="top:234px">Qualified Teachers<p>Lorem ipsum dolor sit amet, consectetur adipiscing elit, sed do eiusmod tempor incididunt ut labore et dolore magna aliqua. Quis ipsum suspendisse ultrices gravida. Risus commodo viverra maecenas accumsan lacus vel facilisis.</p></div>
  </div>
</section>
<div class="partner" style="left:206px"><i></i>PostLark</div>
<div class="partner" style="left:512px"><i></i>SendNest</div>
<div class="partner" style="left:804px"><i></i>FlowCast</div>

<section class="section touch">
  <h2>Keep In Touch</h2>
  <p>Lorem ipsum dolor sit amet, consectetur adipiscing elit, sed do eiusmod tempor incididunt ut labore et dolore magna aliqua. Quis ipsum suspendisse ultrices gravida. Risus commodo viverra maecenas accuLorem ipsum dolor sit amet, consectetur adipiscing elit, sed do eiusmod tempor incididunt ut labore et dolore magna aliqua. Quis ipsum suspendisse ultrices gravida. Risus commodo viverra maecenas accumsan lacus vel facilisis. msan lacus vel facilisis.</p>
  <div class="field" style="top:88px">First name</div>
  <div class="field" style="top:150px">Last name</div>
  <div class="field" style="top:211px">Email</div>
  <a class="btn-outline join" style="position:absolute">JOIN TODAY</a>
</section>

<footer class="section site-footer">
  <div class="foot-logo"><div class="mark"></div>AL-NOOR<br><span style="font-size:9px">ARABIC ACADEMY</span></div>
  <div class="ring" style="left:325px;top:52px"><svg width="12" height="18" viewBox="0 0 12 18"><rect x="1" y="1" width="10" height="16" rx="2" fill="none" stroke="#fff" stroke-width="2"/></svg></div>
  <div class="foot-text" style="left:380px;top:66px">Tap-To-Call: (555) 014 2290</div>
  <div class="ring" style="left:574px;top:52px"><svg width="18" height="14" viewBox="0 0 18 14"><rect x="1" y="1" width="16" height="12" fill="none" stroke="#fff" stroke-width="2"/><path d="M1 1l8 6 8-6" fill="none" stroke="#fff" stroke-width="2"/></svg></div>
  <div class="foot-text" style="left:632px;top:66px">Email : info@alnoorarabic.com</div>
  <div class="ring" style="left:868px;top:52px">Chat</div>
  <div class="ring" style="left:915px;top:52px">Post</div>
  <div class="ring" style="left:963px;top:52px">Pics</div>
  <div class="ring" style="left:1012px;top:52px">Feed</div>
  <div class="copy">Copyrights @ 2020 Al Noor.All Rights Reserved &nbsp;|&nbsp; Privacy Policy &nbsp;|&nbsp; Sitemap</div>
</footer>

</body>
</html>
```